Tech business card design

We need an amazing business card design for our new business 'Pexla' a marketing tech startup based in Sydney, Australia. We provide an online marketplace for businesses to search and buy advertising media, connect with service providers and learn more about marketing. We wish to communicate 'cool tech', reliability and professionalism and design based around our logo.

Target Market(s)

Business Owners

Contact Information for Business Card

Name
Position
Email Address
Website
Phone Number

Font styles to use
Other font styles liked:
• Avenir & Avenir Next

Colors

Designer to choose colors to be used in the design.

```html
<!DOCTYPE html>
<html lang="en">
<head>
<meta charset="utf-8">
<title>Pexla Business Card</title>
<link href="https://fonts.googleapis.com/css2?family=Nunito+Sans:wght@400;700;800&display=swap" rel="stylesheet">
<style>
  :root {
    --stage: #1b1b1e;
    --card: #26292b;
    --card-edge: #303335;
    --ink-light: #f2f2f4;
    --ink-muted: #b9bcc0;
    --ink-dark: #111214;
    --rule: #8d9094;
  }
  * { box-sizing: border-box; margin: 0; padding: 0; }
  html, body {
    width: 1200px;
    height: 800px;
    overflow: hidden;
    background: var(--stage);
    font-family: "Nunito Sans", "Avenir Next", Avenir, sans-serif;
  }
  .canvas {
    position: relative;
    width: 1200px;
    height: 800px;
  }
  .card {
    position: absolute;
    width: 520px;
    height: 298px;
    background: var(--card);
    border: 1px solid var(--card-edge);
    border-radius: 4px;
    box-shadow: 0 18px 40px rgba(0,0,0,0.45);
  }
  .card--front { left: 50px; top: 251px; }
  .card--back { left: 630px; top: 251px; }

  .wordmark {
    font-weight: 800;
    letter-spacing: -1px;
    line-height: 1;
  }
  .card--front .wordmark {
    position: absolute;
    left: 0; right: 0; top: 112px;
    text-align: center;
    font-size: 72px;
    color: var(--ink-dark);
  }
  .card--back .wordmark {
    position: absolute;
    left: 36px; bottom: 38px;
    font-size: 56px;
    color: var(--ink-light);
  }

  .divider {
    position: absolute;
    left: 262px; top: 70px;
    width: 1px; height: 168px;
    background: var(--rule);
  }

  .contact {
    position: absolute;
    left: 286px; top: 74px;
    color: var(--ink-light);
  }
  .contact__name {
    font-size: 17px;
    font-weight: 700;
    line-height: 1.1;
  }
  .contact__role {
    font-size: 12px;
    color: var(--ink-muted);
    margin-bottom: 16px;
  }
  .contact__list { list-style: none; }
  .contact__item {
    display: flex;
    align-items: center;
    gap: 8px;
    font-size: 12px;
    line-height: 1;
    margin-bottom: 9px;
  }
  .contact__icon { width: 16px; height: 16px; flex: none; }
</style>
</head>
<body>
<main class="canvas">
  <section class="card card--front" aria-label="Card front">
    <div class="wordmark">Pexla</div>
  </section>

  <section class="card card--back" aria-label="Card back">
    <div class="wordmark">Pexla</div>
    <div class="divider"></div>
    <div class="contact">
      <p class="contact__name">Liam Carter</p>
      <p class="contact__role">Manager</p>
      <ul class="contact__list">
        <li class="contact__item">
          <svg class="contact__icon" viewBox="0 0 16 16" aria-hidden="true">
            <circle cx="8" cy="8" r="8" fill="#f2f2f4"/>
            <path d="M5.3 4.3l1.4-.3.8 2-1 .7c.5 1.1 1.3 1.9 2.4 2.4l.7-1 2 .8-.3 1.4c-3.3.3-6.3-2.7-6-6z" fill="#26292b"/>
          </svg>
          <span>02.8123.4567</span>
        </li>
        <li class="contact__item">
          <svg class="contact__icon" viewBox="0 0 16 16" aria-hidden="true">
            <circle cx="8" cy="8" r="8" fill="#f2f2f4"/>
            <rect x="4" y="5.2" width="8" height="5.6" rx="0.6" fill="#26292b"/>
            <path d="M4.4 5.6L8 8.4l3.6-2.8" fill="none" stroke="#f2f2f4" stroke-width="0.8"/>
          </svg>
          <span>hello@pexlamedia.com</span>
        </li>
        <li class="contact__item">
          <svg class="contact__icon" viewBox="0 0 16 16" aria-hidden="true">
            <circle cx="8" cy="8" r="8" fill="#f2f2f4"/>
            <g fill="none" stroke="#26292b" stroke-width="0.9">
              <circle cx="8" cy="8" r="4"/>
              <ellipse cx="8" cy="8" rx="1.7" ry="4"/>
              <path d="M4 8h8"/>
            </g>
          </svg>
          <span>www.pexlamedia.com</span>
        </li>
      </ul>
    </div>
  </section>
</main>
</body>
</html>
```